Business Card Design for BrightvaleMedia.com

--I need a business card design for my company BrightvaleMedia.com

I have attached my logo...I want the brightvale media logo on the front of the business card, and then I want The Quillstone Chief on the back of it with my information.

I would like to see a light colored background as well as a dark colored background

FRONT:
BRIGHTVALE MEDIA LOGO
248 N. Larkmoor
3rd Floor
San Diego CA 92173
www.BrightvaleMedia.com

Advanced Website & App Development
Websites, Apps, Online Voucher Systems

Leading Edge Marketing Services
SMS, VB, SMM, SEM,

BACK:
QUILLSTONE CHIEF LOGO
Dorian Pelletta
The Quillstone Chief
Call Or Text: 619-555-0148
Dorian@QuillstoneChief.example
www.QuillstoneChief.example

Target Market(s)

small business owners

Industry/Entity Type

Business Consultant

Contact Information for Business Card

FRONT:
BRIGHTVALE MEDIA LOGO
248 N. Larkmoor
3rd Floor
San Diego CA 92173
www.BrightvaleMedia.com

SMS, VB, SMM, SEM,

BACK:
QUILLSTONE CHIEF LOGO
Dorian Pelletta
The Quillstone Chief
Dorian@QuillstoneChief.example
www.QuillstoneChief.example

Requirements
Must have
• add this quote on it somewhere, anywhere,preferrably on back
• "The Fastest Way To Success Is To Take Action”
• — Dorian Pelletta, Quillstone Chief
Nice to have
• open
Should not have
• red

```html
<!DOCTYPE html>
<html lang="en">
<head>
<meta charset="utf-8">
<title>Brightvale Media — Business Cards</title>
<link rel="stylesheet" href="https://fonts.googleapis.com/css2?family=Montserrat:wght@400;500;700&display=swap">
<style>
  :root {
    --backdrop: #3a3a3c;
    --card: #050505;
    --brand-blue: #1f7fc0;
    --ink: #f2f2f2;
    --band-white: #ffffff;
    --rule: #d8d8d8;
  }
  * { box-sizing: border-box; margin: 0; padding: 0; }
  html, body { width: 1200px; height: 900px; overflow: hidden; }
  body {
    background: var(--backdrop);
    font-family: "Montserrat", Arial, sans-serif;
    color: var(--ink);
    position: relative;
  }
  .card {
    position: absolute;
    width: 640px;
    height: 366px;
    background: var(--card);
    border-radius: 22px;
    overflow: hidden;
    box-shadow: 0 18px 40px rgba(0,0,0,.45);
  }
  .card--front { left: 60px; top: 50px; }
  .card--back { left: 500px; top: 484px; }

  .edge-bands { position: absolute; left: 0; bottom: 0; width: 100%; height: 40px; }

  /* front */
  .brand-name {
    position: absolute;
    left: 0; right: 0; top: 46px;
    text-align: center;
    font-size: 46px;
    font-weight: 500;
    letter-spacing: 4px;
    color: var(--brand-blue);
  }
  .address {
    position: absolute;
    left: 0; right: 0; top: 126px;
    text-align: center;
    font-size: 15px;
    line-height: 20px;
  }
  .accent { color: var(--brand-blue); }
  .services {
    position: absolute;
    left: 42px; top: 228px;
    font-size: 15px;
    line-height: 19px;
  }
  .services strong { font-weight: 700; display: block; }

  /* back */
  .chief-name {
    position: absolute;
    left: 44px; top: 140px;
    font-size: 38px;
    font-weight: 500;
    letter-spacing: 3px;
    color: var(--brand-blue);
  }
  .name-tab {
    position: absolute;
    right: 0; top: 44px;
    width: 22px; height: 34px;
    background: var(--brand-blue);
  }
  .person {
    position: absolute;
    right: 38px; top: 42px;
    text-align: right;
  }
  .person__name { font-size: 24px; font-weight: 700; color: var(--brand-blue); }
  .person__title { font-size: 13px; margin-top: 2px; }
  .divider {
    position: absolute;
    left: 44px; right: 34px; top: 210px;
    height: 2px;
    background: var(--rule);
  }
  .contact {
    position: absolute;
    left: 44px; top: 222px;
    list-style: none;
    font-size: 16px;
    line-height: 22px;
  }
  .contact li { display: flex; align-items: center; gap: 9px; }
  .contact svg { width: 11px; height: 11px; fill: var(--brand-blue); flex: none; }
  .quote {
    position: absolute;
    right: 34px; top: 298px;
    font-size: 14px;
    line-height: 18px;
    letter-spacing: .3px;
    text-transform: uppercase;
    white-space: nowrap;
  }
</style>
</head>
<body>

<section class="card card--front" aria-label="Front of card">
  <div class="brand-name">BRIGHTVALE MEDIA</div>
  <p class="address">
    248 N. Larkmoor<br>
    3rd Floor<br>
    San Diego CA 92173<br>
    www.<span class="accent">BrightvaleMedia</span>.com
  </p>
  <p class="services">
    Advanced Website &amp; App Development<br>
    Websites, Apps, Online Voucher Systems
    <strong>LEADING EDGE MARKETING SERVICES</strong>
    <strong>SMS, VB, SMM, SEM,</strong>
  </p>
  <svg class="edge-bands" viewBox="0 0 640 40" preserveAspectRatio="none">
    <rect x="0" y="24" width="390" height="16" fill="var(--brand-blue)"/>
    <rect x="390" y="10" width="250" height="18" fill="var(--band-white)"/>
  </svg>
</section>

<section class="card card--back" aria-label="Back of card">
  <div class="name-tab"></div>
  <div class="person">
    <div class="person__name">Dorian Pelletta</div>
    <div class="person__title">CEO</div>
  </div>
  <div class="chief-name">QUILLSTONE CHIEF</div>
  <div class="divider"></div>
  <ul class="contact">
    <li><svg viewBox="0 0 12 12"><path d="M2.5 0.5l2 2.5-1.2 1.3c.7 1.6 2 2.9 3.6 3.6l1.3-1.2 2.5 2-1.3 2.3C5 10.5 1.5 7 0.2 1.8z"/></svg><span>619-555-0148</span></li>
    <li><svg viewBox="0 0 12 12"><path d="M0 2h12v8H0zM1 3v.4l5 3.2 5-3.2V3zM1 4.6V9h10V4.6L6 7.8z"/></svg><span>Dorian@QuillstoneChief.example</span></li>
    <li><svg viewBox="0 0 12 12"><circle cx="6" cy="6" r="5.5"/></svg><span>www.<span class="accent">QuillstoneChief</span>.example</span></li>
  </ul>
  <p class="quote">The fastest way to success is to take action</p>
  <svg class="edge-bands" viewBox="0 0 640 40" preserveAspectRatio="none">
    <rect x="0" y="24" width="390" height="16" fill="var(--brand-blue)"/>
    <rect x="390" y="10" width="250" height="18" fill="var(--band-white)"/>
  </svg>
</section>

</body>
</html>
```